Accounting firm needing business card / letterhead designed
Marcus L. Trenholm, CPA
marcus@veltrowledger.com
www.veltrowledger.com
842 E Alder Ave Carrowmere, KY 43827
419-562-0974

```html
<!DOCTYPE html>
<html lang="en">
<head>
<meta charset="utf-8">
<title>Veltrow Ledger – Business Card</title>
<link rel="stylesheet" href="https://fonts.googleapis.com/css2?family=Roboto:wght@400;500&family=Roboto+Condensed:wght@500&display=swap">
<style>
  :root {
    --backdrop: #2b2b2d;
    --card: #1d1d1f;
    --card-edge: #262628;
    --accent-green: #8fd13a;
    --accent-violet: #3b34a8;
    --text-light: #ececec;
    --divider: #9a9a9a;
  }
  * { box-sizing: border-box; margin: 0; padding: 0; }
  html, body {
    width: 1200px; height: 900px; overflow: hidden;
    background: var(--backdrop);
  }
  .stage {
    width: 1200px; height: 900px;
    display: flex; flex-direction: column; align-items: center; justify-content: center;
    gap: 40px;
  }
  .card {
    position: relative;
    width: 700px; height: 400px;
    background: var(--card);
    border: 1px solid var(--card-edge);
    box-shadow: 0 10px 30px rgba(0,0,0,.45);
  }
  /* Front */
  .card-front { display: flex; flex-direction: column; align-items: center; justify-content: center; }
  .brand-name {
    font-family: "Roboto", sans-serif; font-weight: 500;
    font-size: 52px; letter-spacing: 6px; text-transform: uppercase;
    color: var(--accent-violet);
  }
  .front-web {
    margin-top: 56px;
    font-family: "Roboto", sans-serif; font-size: 16px;
    letter-spacing: 9px; color: var(--text-light);
  }
  /* Back */
  .holder-name {
    position: absolute; left: 50px; top: 140px;
    font-family: "Roboto Condensed", sans-serif; font-weight: 500;
    font-size: 28px; line-height: 1.2; color: var(--accent-green);
    white-space: nowrap;
  }
  .divider {
    position: absolute; left: 392px; top: 108px;
    width: 2px; height: 96px; background: var(--divider);
  }
  .contact-list {
    position: absolute; left: 418px; top: 116px;
    list-style: none;
    font-family: "Roboto", sans-serif; font-size: 18px; color: var(--text-light);
  }
  .contact-list li { display: flex; align-items: center; gap: 10px; height: 26px; white-space: nowrap; }
  .contact-list svg { width: 16px; height: 16px; fill: var(--accent-green); flex: none; }
  .address {
    position: absolute; left: 0; right: 0; top: 288px;
    display: flex; justify-content: center; align-items: center; gap: 6px;
    font-family: "Roboto", sans-serif; font-size: 19px; color: var(--text-light);
  }
  .address svg { width: 16px; height: 20px; fill: var(--accent-green); }
</style>
</head>
<body>
<main class="stage">
  <section class="card card-front">
    <div class="brand-name">Veltrow Ledger</div>
    <div class="front-web">www.veltrowledger.com</div>
  </section>

  <section class="card card-back">
    <h1 class="holder-name">Marcus L. Trenholm, CPA</h1>
    <div class="divider"></div>
    <ul class="contact-list">
      <li>
        <svg viewBox="0 0 24 24" aria-hidden="true"><path d="M6.6 10.8a15.1 15.1 0 0 0 6.6 6.6l2.2-2.2c.3-.3.7-.4 1-.2 1.1.4 2.3.6 3.6.6.6 0 1 .4 1 1V20c0 .6-.4 1-1 1A17 17 0 0 1 3 4c0-.6.4-1 1-1h3.5c.6 0 1 .4 1 1 0 1.3.2 2.5.6 3.6.1.3 0 .7-.2 1z"/></svg>
        419-562-0974
      </li>
      <li>
        <svg viewBox="0 0 24 24" aria-hidden="true"><path d="M2 5h20v14H2z M3.5 6.5 12 13l8.5-6.5" stroke="#1d1d1f" stroke-width="1.6"/></svg>
        marcus@veltrowledger.com
      </li>
      <li>
        <svg viewBox="0 0 24 24" aria-hidden="true"><circle cx="12" cy="12" r="10"/><path d="M2 12h20M12 2c3 3 3 17 0 20M12 2c-3 3-3 17 0 20" stroke="#1d1d1f" stroke-width="1.4" fill="none"/></svg>
        www.veltrowledger.com
      </li>
    </ul>
    <p class="address">
      <svg viewBox="0 0 16 20" aria-hidden="true"><path d="M8 0a7 7 0 0 0-7 7c0 5 7 13 7 13s7-8 7-13a7 7 0 0 0-7-7zm0 10a3 3 0 1 1 0-6 3 3 0 0 1 0 6z"/></svg>
      842 E Alder Ave, Carrowmere, KY 43827
    </p>
  </section>
</main>
</body>
</html>
```